Full Business Set-Up Stationary, Folder, Envelope, & Business Card, etc. CPA Firm
CPA Firm Collarteral Package
Full Business Set-Up Stationary, Folder, Envelope, & Business Card, etc. CPA Firm - Consulting
Creative Brief
Bright & Fun-filled
Mara Benton, CPA
Certified Public Accountant
512 Wexford Lane Suite 200 Brandon, FL 33571
MaraBenton@ledgerwisemail.com
www.MaraBentonCPA-example.com
AC58163
Key Words: CPA since 1999 Servicing State of Florida since 1999 Certified Management Accountant Certified Public Accounting Firm Award Winning CPA Award Winning Professional Officies Located in the Hillcrest Merchants Guild Building Trustworthy, Professional, Experienced
Tag Line: See the Clear Path Steadfast Services
marabenton marabenton
Thanks for your submissions. Please include portfolio for the Firm. Particularly a Business Folder and Letterhead/Envelope. Ipad and Iphone Designs.

```html
<!DOCTYPE html>
<html lang="en">
<head>
<meta charset="utf-8">
<title>Mara Benton CPA – Business Card</title>
<link href="https://fonts.googleapis.com/css2?family=Cinzel:wght@400;600&family=EB+Garamond:wght@400;500&display=swap" rel="stylesheet">
<style>
  :root{
    --backdrop:#e4e6e9;
    --blue-light:#4a9be0;
    --blue-deep:#1c62bd;
    --blue-ink:#2b6cc4;
    --green:#7dc142;
    --white:#ffffff;
    --ink:#2f3a45;
    --muted:#6b7885;
  }
  *{margin:0;padding:0;box-sizing:border-box}
  html,body{width:1200px;height:908px;overflow:hidden;background:var(--backdrop)}
  .canvas{position:relative;width:1200px;height:908px}
  .card{position:absolute;top:304px;width:525px;height:300px;border-radius:18px;overflow:hidden;
        box-shadow:0 6px 18px rgba(0,0,0,.18)}
  /* front */
  .card-front{left:45px;background:linear-gradient(135deg,var(--blue-light),var(--blue-deep))}
  .card-front .mark-circle{position:absolute;right:40px;top:60px;width:180px;height:180px;border-radius:50%;
        background:rgba(255,255,255,.12)}
  .card-front .brand{position:absolute;left:36px;top:118px;color:var(--white)}
  .brand-name{font-family:"Cinzel",serif;font-weight:400;font-size:31px;letter-spacing:.5px;line-height:1;white-space:nowrap}
  .brand-tag{font-family:"Cinzel",serif;font-size:11px;letter-spacing:5.4px;margin-top:8px;text-transform:uppercase;
        border-top:1px solid rgba(255,255,255,.6);padding-top:6px;white-space:nowrap}
  /* back */
  .card-back{left:630px;background:var(--white)}
  .card-back .edge-band{position:absolute;right:0;top:0;width:34px;height:100%;background:var(--blue-deep);
        display:flex;align-items:center;justify-content:center}
  .card-back .web{writing-mode:vertical-rl;transform:rotate(180deg);
        font-family:"EB Garamond",serif;font-size:12px;line-height:1;color:var(--white);letter-spacing:.6px;white-space:nowrap}
  .card-back .swoosh{position:absolute;left:0;bottom:0;width:525px;height:300px}
  .contact{position:absolute;left:250px;top:38px;font-family:"EB Garamond",serif;color:var(--ink)}
  .contact .name{font-family:"Cinzel",serif;font-size:19px;color:var(--blue-ink);white-space:nowrap}
  .contact .title{font-family:"Cinzel",serif;font-size:9.5px;letter-spacing:1.2px;color:var(--muted);margin-bottom:10px;white-space:nowrap}
  .contact .license{font-size:11px;color:var(--green);margin-bottom:6px}
  .contact p{font-size:12.5px;line-height:1.35;white-space:nowrap}
  .logo-block{position:absolute;left:34px;top:160px;display:flex;flex-direction:column;align-items:flex-start}
  .logo-dot{width:44px;height:44px;border-radius:50%;background:var(--blue-ink);margin:0 0 8px 58px}
  .logo-block .brand-name{font-size:20px;color:var(--blue-ink)}
  .logo-block .brand-tag{font-size:7.5px;letter-spacing:3.6px;color:var(--green);border-top:1px solid var(--green);margin-top:4px;padding-top:3px}
</style>
</head>
<body>
<main class="canvas">
  <section class="card card-front">
    <div class="mark-circle"></div>
    <div class="brand">
      <div class="brand-name">MARA BENTON CPA</div>
      <div class="brand-tag">See the Clear Path</div>
    </div>
  </section>

  <section class="card card-back">
    <svg class="swoosh" viewBox="0 0 525 300" aria-hidden="true">
      <path d="M200 300 C330 270 440 200 525 120 L525 150 C450 225 350 280 250 300 Z" fill="var(--green)"/>
      <path d="M250 300 C360 280 455 220 525 150 L525 300 Z" fill="var(--blue-deep)"/>
    </svg>
    <div class="edge-band">
      <div class="web">www.MaraBentonCPA-example.com</div>
    </div>

    <div class="contact">
      <div class="name">MARA BENTON, CPA</div>
      <div class="title">CERTIFIED PUBLIC ACCOUNTANT</div>
      <div class="license">License No. AC58163</div>
      <p>512 Wexford Lane Suite 200</p>
      <p>Brandon, FL 33571</p>
      <p>P: 813-555-0142</p>
      <p>F: 813-555-0178</p>
      <p>MaraBenton@ledgerwisemail.com</p>
    </div>

    <div class="logo-block">
      <div class="logo-dot"></div>
      <div class="brand-name">MARA BENTON CPA</div>
      <div class="brand-tag">See the Clear Path</div>
    </div>
  </section>
</main>
</body>
</html>
```